Wordpress Template Design using existing Logo and Colors

We are wanting a wordpress theme designing for our b2b marketing consultancy business. A comprehesive and elagant design to our current site www.plovtrix.com would be good.

Industry/Entity Type

Marketing

Font styles to use
Sans Serif

```html
<!DOCTYPE html>
<html lang="en">
<head>
<meta charset="utf-8">
<title>Plovtrix – B2B Data &amp; Marketing</title>
<link href="https://fonts.googleapis.com/css2?family=Open+Sans:wght@400;600&display=swap" rel="stylesheet">
<style>
:root{
  --red:#e61b23;
  --red-dark:#b5161c;
  --slate:#4d5a72;
  --ink:#222;
  --grey-bg:#f3f3f3;
  --footer:#474747;
  --footer-text:#c9c9c9;
  --social:#e6e6e6;
}
*{box-sizing:border-box;margin:0;padding:0}
html,body{width:782px;height:1200px;overflow:hidden;background:#fff;font-family:'Open Sans',sans-serif;color:var(--ink)}
.page{position:relative;width:782px;height:1200px}
.site-header{position:absolute;top:0;left:0;width:782px;height:83px}
.brand{position:absolute;left:86px;top:36px}
.brand-name{font-size:24px;font-weight:600;color:var(--red);letter-spacing:3px;line-height:30px}
.social-top{position:absolute;right:87px;top:21px;display:flex;gap:10px}
.social-box{width:21px;height:21px;background:var(--social)}
.main-nav{position:absolute;right:87px;top:60px;display:flex;gap:20px;font-size:8px;color:#555}
.main-nav .active{color:var(--red)}
.hero{position:absolute;top:83px;left:0;width:782px;height:317px;background:linear-gradient(90deg,#e9ecef 0%,#d9d6d3 45%,#9aa3b4 80%,#d8dce2 100%)}
.hero-card{position:absolute;left:86px;top:74px;width:209px;height:170px;background:rgba(92,103,125,.9);color:#fff;padding:17px 14px}
.hero-card h1{font-size:13px;font-weight:600;line-height:17px;margin-bottom:12px}
.hero-card p{font-size:7px;line-height:12.5px;margin-bottom:12px}
.btn-light{display:inline-block;background:#fff;color:var(--red);font-size:7px;padding:9px 11px}
.slider-arrow{position:absolute;top:150px;width:18px;height:18px;background:#8a8f98}
.slider-arrow.prev{left:0}.slider-arrow.next{right:0}
.intro{position:absolute;top:446px;left:86px;width:610px;text-align:center;font-size:12.6px;line-height:20px}
.services{position:absolute;top:521px;left:86px;width:304px;height:260px;background:var(--red);border-right:7px solid var(--red-dark)}
.services ul{list-style:none;padding:20px 0 0 19px}
.services li{display:flex;align-items:center;gap:10px;height:59px;color:#fff;font-size:15px;font-weight:600}
.icon-box{width:42px;height:42px;background:#fff;display:flex;align-items:center;justify-content:center}
.services-pointer{position:absolute;left:0;top:29px;width:0;height:0;border-top:12px solid transparent;border-bottom:12px solid transparent;border-left:12px solid #fff}
.feature{position:absolute;top:521px;left:390px;width:305px;height:260px;background:var(--slate);color:#fff;padding:20px 21px}
.feature-photo{width:264px;height:146px;background:linear-gradient(120deg,#1e3550,#3d5d83 50%,#b07058);margin-bottom:20px}
.feature p{font-size:8px;line-height:13.5px;margin-bottom:6px}
.feature a{font-size:8px;color:#fff}
.brochure{position:absolute;top:781px;left:86px;width:610px;height:167px;background:var(--grey-bg);text-align:center;padding-top:37px}
.brochure h2{font-size:15px;font-weight:400;color:var(--red);margin-bottom:4px}
.brochure p{font-size:10.5px;line-height:14.5px;padding:0 15px;margin-bottom:10px}
.btn-slate{display:inline-block;background:var(--slate);color:#fff;font-size:10.5px;padding:6px 11px}
.site-footer{position:absolute;top:1000px;left:0;width:782px;height:172px;background:var(--footer);color:#fff}
.foot-col{position:absolute;top:38px}
.foot-col h3{font-size:12.5px;font-weight:600;margin-bottom:8px}
.foot-col li{list-style:none;font-size:7px;color:var(--footer-text);height:14.5px;display:flex;gap:8px;align-items:center}
.foot-col li svg{flex:none}
.social-foot{display:flex;gap:10px}
.copyright{position:absolute;top:1172px;left:0;width:782px;height:28px;text-align:center;font-size:7px;line-height:28px;color:#444}
</style>
</head>
<body>
<div class="page">
  <header class="site-header">
    <div class="brand"><span class="brand-name">PLOVTRIX</span></div>
    <div class="social-top"><span class="social-box"></span><span class="social-box"></span><span class="social-box"></span><span class="social-box"></span></div>
    <nav class="main-nav"><span class="active">HOME</span><span>ABOUT US</span><span>TARGET MARKETING</span><span>DATA MANAGEMENT</span><span>CONTACT US</span></nav>
  </header>

  <section class="hero" role="img" aria-label="Two colleagues reviewing documents in a bright office">
    <div class="hero-card">
      <h1>REACH THE RIGHT PEOPLE, WITH THE RIGHT MESSAGE, AT THE RIGHT TIME</h1>
      <p>Whether your aim is to acquire new customers, re-engage existing, or grow their value over time, Plovtrix offers tailored solutions.</p>
      <span class="btn-light">Learn More</span>
    </div>
    <span class="slider-arrow prev"><svg width="18" height="18"><path d="M12 9H6M9 6L6 9l3 3" stroke="#fff" stroke-width="1.6" fill="none"/></svg></span>
    <span class="slider-arrow next"><svg width="18" height="18"><path d="M6 9h6M9 6l3 3-3 3" stroke="#fff" stroke-width="1.6" fill="none"/></svg></span>
  </section>

  <p class="intro">We are a B2B Data, Analytics and Marketing Consulting Company specialized in harnessing the power of potential data to strengthen connections between decisions makers, companies and products. We focus on solutions engineered to solve distinct challenges in the data, direct marketing, and analytics space.</p>

  <section class="services">
    <span class="services-pointer"></span>
    <ul>
      <li><span class="icon-box"><svg width="26" height="26" fill="none" stroke="#e61b23" stroke-width="1.4"><ellipse cx="13" cy="6" rx="10" ry="3"/><path d="M3 6v14c0 1.7 4.5 3 10 3s10-1.3 10-3V6M3 11c0 1.7 4.5 3 10 3s10-1.3 10-3M3 15.5c0 1.7 4.5 3 10 3s10-1.3 10-3"/></svg></span>B2B DATABASE</li>
      <li><span class="icon-box"><svg width="28" height="28" fill="none" stroke="#e61b23" stroke-width="1.6"><circle cx="14" cy="14" r="12"/><circle cx="14" cy="14" r="8"/><circle cx="14" cy="14" r="4"/></svg></span>TARGET MARKETING</li>
      <li><span class="icon-box"><svg width="28" height="28" fill="none" stroke="#e61b23" stroke-width="1.4"><path d="M6 15v-3a8 8 0 0116 0v3"/><rect x="4" y="14" width="4" height="7" rx="2"/><rect x="20" y="14" width="4" height="7" rx="2"/><path d="M22 21c0 3-4 4-7 4"/></svg></span>CALL CENTER</li>
      <li><span class="icon-box"><svg width="30" height="30"><g fill="#e61b23" font-family="Open Sans,sans-serif" font-size="7.5" font-weight="600"><text x="5" y="9">1010</text><text x="5" y="17">0001</text><text x="5" y="25">1100</text></g><path d="M4 2H2v26h2M26 2h2v26h-2" stroke="#e61b23" fill="none"/></svg></span>DATA MANAGEMENT</li>
    </ul>
  </section>

  <section class="feature">
    <div class="feature-photo" role="img" aria-label="Technician working beside server racks in a data center"></div>
    <p>Get access to Asia’s leading market &amp; business intelligence database over 1,500,000 organizations and 3,500,000 decision makers.</p>
    <a href="#">Read more</a>
  </section>

  <section class="brochure">
    <h2>CORPORATE BROCHURE</h2>
    <p>Learn our leading target marketing and intelligent data management solutions to attain new customers for your niche products and services.</p>
    <span class="btn-slate">Download Now</span>
  </section>

  <footer class="site-footer">
    <div class="foot-col" style="left:86px">
      <h3>GLOBAL HQ</h3>
      <ul>
        <li><svg width="6" height="6"><path d="M1 0h2l1 2-1 1 2 2 1-1 1 1v1H5C3 6 0 3 0 1z" fill="#aaa"/></svg>+1 (555) 014-2290</li>
        <li><svg width="7" height="6"><rect width="7" height="5" y="0.5" fill="#aaa"/></svg>hello.us@plovtrix.com</li>
        <li><svg width="7" height="7"><circle cx="3.5" cy="3.5" r="3.2" fill="#aaa"/></svg>www.plovtrix.com</li>
        <li><svg width="7" height="7"><circle cx="3.5" cy="3.5" r="3" fill="none" stroke="#aaa"/></svg>Monday – Friday : 9AM – 6PM</li>
        <li><svg width="6" height="7"><path d="M3 7L0.5 3A2.5 2.5 0 115.5 3z" fill="#aaa"/></svg>418 Harbor View Lane, Suite 210, Marlow Bay, CA 90000, USA</li>
      </ul>
    </div>
    <div class="foot-col" style="left:346px">
      <h3>REGIONAL HQ</h3>
      <ul>
        <li><svg width="6" height="6"><path d="M1 0h2l1 2-1 1 2 2 1-1 1 1v1H5C3 6 0 3 0 1z" fill="#aaa"/></svg>+65 5550 1847</li>
        <li><svg width="7" height="6"><rect width="7" height="5" y="0.5" fill="#aaa"/></svg>hello.sg@plovtrix.com</li>
        <li><svg width="7" height="7"><circle cx="3.5" cy="3.5" r="3.2" fill="#aaa"/></svg>www.plovtrix.com</li>
        <li><svg width="7" height="7"><circle cx="3.5" cy="3.5" r="3" fill="none" stroke="#aaa"/></svg>Monday – Friday : 9AM – 6PM</li>
        <li><svg width="6" height="7"><path d="M3 7L0.5 3A2.5 2.5 0 115.5 3z" fill="#aaa"/></svg>22 Kestrel Avenue, #08-04 Lumen Hub, Singapore 400000</li>
      </ul>
    </div>
    <div class="foot-col" style="left:580px">
      <h3>FOLLOW US ON</h3>
      <div class="social-foot"><span class="social-box"></span><span class="social-box"></span><span class="social-box"></span><span class="social-box"></span></div>
    </div>
  </footer>
  <div class="copyright">Copyright © 2018 Plovtrix. All rights reserved.</div>
</div>
</body>
</html>
```